Business Card Design for Training Business

Clear Path Coaching is a new business that delivers training and other services with a focus on topics related to mental health and wellbeing, for example, Wellmind Response Course, Resilience etc. We have a strong focus on evidence-based psychology and neuroscience. I have a logo which I will upload with the brief, so please consider colours that work well with the logo.
Target Market(s)
Adults, workplaces (particularly government and not-for-profits)
Industry/Entity Type
Business
Contact Information for Business Card
Head Strong TrainingSamantha SellwoodDirector0438 770 850sam@headstrongtraining.com.auwww.headstrongtraining.com.au

```html
<!DOCTYPE html>
<html lang="en">
<head>
<meta charset="UTF-8">
<title>Clear Path Coaching — Business Card</title>
<link rel="stylesheet" href="https://fonts.googleapis.com/css2?family=Questrial&display=swap">
<style>
  :root {
    --backdrop: #3a3a3a;
    --teal: #25b8be;
    --teal-line: #2bb5bb;
    --ring-grey: #5a5552;
    --paper: #f7f7f6;
    --ink-light: #ffffff;
    --ink-grey: #7a716c;
  }
  * { margin: 0; padding: 0; box-sizing: border-box; }
  html, body {
    width: 1200px;
    height: 750px;
    overflow: hidden;
    background: var(--backdrop);
    font-family: "Questrial", "Century Gothic", sans-serif;
  }
  .canvas {
    position: relative;
    width: 1200px;
    height: 750px;
  }
  .card {
    position: absolute;
    width: 376px;
    height: 376px;
  }
  .card svg {
    position: absolute;
    inset: 0;
    width: 100%;
    height: 100%;
  }
  .card--contact { left: 214px; top: 170px; }
  .card--brand   { left: 620px; top: 172px; }

  .contact {
    position: absolute;
    inset: 0;
    color: var(--ink-light);
    text-align: center;
  }
  .contact__name {
    position: absolute;
    left: 0; right: 0;
    top: 113px;
    font-size: 24px;
    letter-spacing: 0.6px;
  }
  .contact__role {
    position: absolute;
    left: 0; right: 0;
    top: 144px;
    font-size: 16px;
  }
  .contact__details {
    position: absolute;
    left: 0; right: 0;
    top: 187px;
    list-style: none;
    font-size: 14.5px;
    line-height: 25.5px;
  }

  .brand__name {
    position: absolute;
    left: 0; right: 0;
    top: 220px;
    text-align: center;
    font-size: 19px;
    letter-spacing: 2.4px;
    color: var(--ink-grey);
  }
</style>
</head>
<body>
<main class="canvas">

  <section class="card card--contact" aria-label="Contact side">
    <svg viewBox="0 0 376 376" role="img" aria-label="Teal card face with a faint geometric pattern">
      <circle cx="188" cy="188" r="188" fill="var(--teal)"/>
      <circle cx="188" cy="188" r="180" fill="none" stroke="var(--ring-grey)" stroke-width="2.5"/>
    </svg>
    <div class="contact">
      <h1 class="contact__name">Rebecca Tanfield</h1>
      <p class="contact__role">Director</p>
      <ul class="contact__details">
        <li class="contact__phone">0491 362 517</li>
        <li class="contact__email">bec@clearpathcoaching.example.au</li>
        <li class="contact__web">www.clearpathcoaching.example.au</li>
      </ul>
    </div>
  </section>

  <section class="card card--brand" aria-label="Brand side">
    <svg viewBox="0 0 376 376">
      <circle cx="188" cy="188" r="186" fill="var(--paper)"/>
      <circle cx="188" cy="188" r="184" fill="none" stroke="var(--teal-line)" stroke-width="4"/>
      <circle class="brand__mark" cx="184" cy="158" r="42" fill="none" stroke="var(--teal-line)" stroke-width="2"/>
    </svg>
    <p class="brand__name">CLEAR PATH COACHING</p>
  </section>

</main>
</body>
</html>
```